Equine Podcast Cover Art Design

We need catchy cover art for a horse related podcast "Ride Onward Together"
Brief show description"
Whether you want to ride to experience horses, develop yourself to the next level as a horseman/horsewoman or ride to improve your physical and mental health, we are committed to helping you Ride Onward TogetherĀ®. Join us as we explore the nuance of equine management and sports as well as interview industry professionals to provide you with the knowledge necessary to be a better partner for your equine friends.
I have uploaded two existing logos we use for various purposes to give you an idea of existing style.
Target Market(s)
Horse owners and other equine professionals
Look and feel
Each slider illustrates characteristics of the customer's brand and the style your logo design should communicate.

```html
<!DOCTYPE html>
<html lang="en">
<head>
<meta charset="utf-8">
<title>Ride Onward Together – Podcast Cover</title>
<link href="https://fonts.googleapis.com/css2?family=Inter:wght@400;500&family=Playfair+Display:wght@800&display=swap" rel="stylesheet">
<style>
  :root {
    --bg: #170d0d;
    --photo-sky: #8a8f86;
    --photo-trees: #2e3a28;
    --photo-horse: #6b3a24;
    --photo-grass: #3d4632;
    --pink: #d59489;
    --white: #ffffff;
  }
  * { margin: 0; padding: 0; box-sizing: border-box; }
  html, body { width: 1200px; height: 1200px; overflow: hidden; background: var(--bg); }
  .cover {
    position: relative;
    width: 1200px;
    height: 1200px;
    background: var(--bg);
    overflow: hidden;
    font-family: "Inter", Arial, sans-serif;
  }
  .cover__photo {
    position: absolute;
    inset: 0 0 280px 0;
    background:
      linear-gradient(to bottom, rgba(23,13,13,0) 45%, var(--bg) 100%),
      linear-gradient(to right, rgba(23,13,13,0.85) 0%, rgba(23,13,13,0.2) 40%, rgba(23,13,13,0) 60%),
      radial-gradient(ellipse 40% 30% at 72% 45%, var(--photo-horse) 0%, rgba(107,58,36,0) 100%),
      linear-gradient(to bottom, var(--photo-sky) 0%, var(--photo-trees) 25%, var(--photo-trees) 55%, var(--photo-grass) 75%);
  }
  .farm-mark {
    position: absolute;
    left: 101px;
    top: 90px;
    width: 218px;
    height: 218px;
    border: 3px solid var(--white);
    border-radius: 50%;
    display: flex;
    align-items: center;
    justify-content: center;
    text-align: center;
  }
  .farm-mark__name {
    color: var(--white);
    font-family: "Inter", Arial, sans-serif;
    font-weight: 500;
    font-size: 24px;
    line-height: 1.15;
    letter-spacing: 0.02em;
    text-transform: uppercase;
  }
  .title {
    position: absolute;
    left: 108px;
    top: 560px;
    line-height: 1;
  }
  .title__line {
    display: block;
    color: var(--pink);
    font-family: "Inter", Arial, sans-serif;
    font-weight: 400;
    font-size: 168px;
    letter-spacing: -0.02em;
    line-height: 174px;
  }
  .title__main {
    display: block;
    margin-top: 14px;
    color: var(--white);
    font-family: "Playfair Display", Georgia, serif;
    font-weight: 800;
    font-size: 148px;
    line-height: 1;
    letter-spacing: 0.01em;
  }
  .title__reg {
    font-family: "Inter", Arial, sans-serif;
    font-weight: 400;
    font-size: 34px;
    vertical-align: 90px;
    margin-left: 6px;
  }
</style>
</head>
<body>
  <main class="cover">
    <div class="cover__photo" role="img" aria-label="Photo of a rider in show attire jumping a bay horse over a wooden fence, trees in the background"></div>

    <div class="farm-mark">
      <span class="farm-mark__name">Evergreen<br>Meadow<br>Farm</span>
    </div>

    <h1 class="title">
      <span class="title__line">Ride</span>
      <span class="title__line">Onward</span>
      <span class="title__main">TOGETHER<span class="title__reg">®</span></span>
    </h1>
  </main>
</body>
</html>
```